Business Card for Coastal Tundrabridge Advisory

We need a business card for Coastal Tundrabridge Advisory. The company website address is provided below. The company logo is attached. We provide specialized permafrost services to the mining, transportation, and oil & gas industries. The card should be prepared for:
Matthias Korhonen, PhD.
Coastal Tundrabridge Advisory
PO Box 418259
Quillwater, Alaska 99642
Direct: +1-907-555-0143
Email: mkorhonen@tundrabridgeadvisory.example
Website: www.coastaltundrabridgeadvisory.example

```html
<!DOCTYPE html>
<html lang="en">
<head>
<meta charset="utf-8">
<title>Coastal Tundrabridge Advisory – Business Card</title>
<link rel="stylesheet" href="https://fonts.googleapis.com/css2?family=Roboto+Condensed:ital,wght@1,700&family=Arimo:wght@400&family=Jost:wght@400&display=swap">
<style>
  :root {
    --page: #ebebeb;
    --card-light: #ffffff;
    --card-dark: #333333;
    --accent-grey: #808080;
    --ink: #1a1a1a;
    --name-ink: #3b3b3b;
    --gold: #a8924f;
  }
  * { margin: 0; padding: 0; box-sizing: border-box; }
  html, body { width: 1200px; height: 1199px; overflow: hidden; background: var(--page); }
  .canvas { position: relative; width: 1200px; height: 1199px; }

  .card { position: absolute; left: 236px; width: 727px; height: 412px; border-radius: 28px; overflow: hidden; }
  .card--front { top: 157px; background: var(--card-light); }
  .card--back { top: 650px; background: var(--card-dark); display: flex; align-items: center; justify-content: center; }

  .side-bar { position: absolute; left: 43px; top: 0; width: 29px; height: 229px; background: var(--accent-grey); }
  .icon-stack { position: absolute; left: 43px; top: 234px; width: 29px; }
  .icon-cell { width: 29px; height: 27px; margin-bottom: 2px; background: var(--accent-grey); display: flex; align-items: center; justify-content: center; }
  .icon-cell:last-child { border-radius: 0 0 14px 14px; }
  .icon-cell svg { width: 13px; height: 13px; }

  .identity { position: absolute; right: 89px; top: 33px; text-align: right; }
  .identity__name { font-family: "Roboto Condensed", sans-serif; font-style: italic; font-weight: 700; font-size: 31px; color: var(--name-ink); line-height: 1.1; }
  .identity__role { font-family: "Arimo", sans-serif; font-size: 15px; color: var(--ink); margin-top: 1px; }

  .profile-tab { position: absolute; right: 0; top: 25px; width: 80px; height: 75px; background: var(--accent-grey); border-radius: 37px 0 0 37px; display: flex; align-items: center; justify-content: center; }
  .profile-tab svg { width: 30px; height: 34px; margin-left: 6px; }

  .address { position: absolute; left: 92px; top: 140px; font-family: "Arimo", sans-serif; font-size: 17px; line-height: 22px; color: var(--ink); }
  .contacts { position: absolute; left: 92px; top: 234px; list-style: none; font-family: "Arimo", sans-serif; font-size: 17px; color: var(--ink); }
  .contacts li { height: 29px; line-height: 27px; }

  .brand-name { font-family: "Jost", sans-serif; font-weight: 400; font-size: 34px; letter-spacing: 5px; color: var(--gold); text-transform: uppercase; white-space: nowrap; }
</style>
</head>
<body>
<main class="canvas">
  <section class="card card--front" aria-label="Business card front">
    <div class="side-bar"></div>
    <div class="icon-stack">
      <div class="icon-cell"><svg viewBox="0 0 16 16"><path fill="#fff" d="M4 1.5l2.2 3-1.3 1.6c.9 1.9 2.3 3.3 4.2 4.2l1.6-1.3 3 2.2-1 2.6C7.6 13.6 2.4 8.4 1.5 2.5z"/></svg></div>
      <div class="icon-cell"><svg viewBox="0 0 16 16"><rect x="4.5" y="1.5" width="7" height="13" rx="1.2" fill="none" stroke="#fff" stroke-width="1.4"/></svg></div>
      <div class="icon-cell"><svg viewBox="0 0 16 16"><rect x="1.5" y="3.5" width="13" height="9" rx="1" fill="#fff"/><path d="M1.5 4l6.5 5 6.5-5" fill="none" stroke="#808080" stroke-width="1.2"/></svg></div>
      <div class="icon-cell"><svg viewBox="0 0 16 16"><circle cx="8" cy="8" r="6.3" fill="none" stroke="#fff" stroke-width="1.4"/><path d="M1.7 8h12.6M8 1.7c-3 3.5-3 9.1 0 12.6M8 1.7c3 3.5 3 9.1 0 12.6" fill="none" stroke="#fff" stroke-width="1.1"/></svg></div>
    </div>

    <div class="identity">
      <p class="identity__name">Matthias Korhonen, PhD</p>
      <p class="identity__role">Founder &amp; Director</p>
    </div>
    <div class="profile-tab">
      <svg viewBox="0 0 30 34"><circle cx="15" cy="9" r="7" fill="#fff"/><path d="M2 33c0-8 5.5-13 13-13s13 5 13 13z" fill="#fff"/></svg>
    </div>

    <address class="address" style="font-style:normal">
      PO Box 418259<br>
      Quillwater, Alaska 99642
    </address>
    <ul class="contacts">
      <li>+1-907-555-0143</li>
      <li>(907) 555 0178</li>
      <li>mkorhonen@tundrabridgeadvisory.example</li>
      <li>www.coastaltundrabridgeadvisory.example</li>
    </ul>
  </section>

  <section class="card card--back" aria-label="Business card back">
    <p class="brand-name">Coastal Tundrabridge Advisory</p>
  </section>
</main>
</body>
</html>
```